Technical Communications firm needs an article turned into a white paper

We want to redesign a 3-part blog series into a white paper that we can print for a conference. I've consolidated the three posts into the attached Word document.

We are looking for a light, easy to read design. Good use of graphics to support the message. I've added the graphics we used in the original post.

You can view them at
http://www.brightquillpages.com/blog/are-you-satisfied-with-your-dita-solution/

Target Market(s)

Product managers from High-tech, Finance, and Medical industries.

Industry/Entity Type

Information Technology

Colors

Designer to choose colors to be used in the design.

Requirements
Must have
• Must be modern, light, easy to read and slick design. Try to incorporate the graphics provided, but feel free to add more. Must retain the lists and tables.
• Must align with our website/brand.
• Must be easy to read. So not too busy.
• Please move all footnotes to endnotes. You'll need to rework the numbering.
Nice to have
• Awesome coverpage.
Should not have
• Hokey clipart. Not too heavy or hard to read.

```html
<!DOCTYPE html>
<html lang="en">
<head>
<meta charset="utf-8">
<title>Are You Satisfied With Your DITA Solution?</title>
<link rel="stylesheet" href="https://fonts.googleapis.com/css2?family=Montserrat:wght@300;400;600;700;800&display=swap">
<style>
  :root {
    --bg: #e9e9e9;
    --paper: #ffffff;
    --brand-blue: #049fd3;
    --brand-navy: #1f2a6b;
    --slate: #4f5a62;
    --slate-dark: #3c454c;
    --ink: #5c5f63;
    --ink-soft: #8a8d90;
  }
  * { box-sizing: border-box; margin: 0; padding: 0; }
  html, body {
    width: 1200px; height: 960px; overflow: hidden;
    background: var(--bg);
    font-family: "Montserrat", Arial, sans-serif;
  }
  .page {
    position: absolute; left: 270px; top: 40px;
    width: 660px; height: 880px;
    background: var(--paper);
    overflow: hidden;
    box-shadow: 0 6px 24px rgba(0,0,0,.12);
  }
  .hero-photo {
    position: absolute; left: 0; top: 0; width: 100%; height: 410px;
    background: linear-gradient(100deg, var(--slate-dark) 0%, var(--slate) 55%, #6a7278 100%);
  }
  .social-tab {
    position: absolute; right: 0; top: 0;
    width: 150px; height: 44px;
    background: var(--brand-blue);
    border-bottom-left-radius: 44px;
  }
  .running-head {
    position: absolute; right: 160px; top: 16px;
    font-size: 7px; font-weight: 600; letter-spacing: .3px;
    color: #e8eef1; text-transform: uppercase;
  }
  .title-disc {
    position: absolute; left: 40px; top: 250px;
    width: 300px; height: 300px; border-radius: 50%;
    background: var(--brand-blue);
  }
  .title {
    position: absolute; left: 66px; top: 338px; width: 270px;
    color: #fff; font-weight: 800; font-size: 21px; line-height: 1.55;
    text-transform: uppercase; letter-spacing: .2px; white-space: nowrap;
  }
  .intro {
    position: absolute; left: 370px; top: 436px; width: 260px;
    font-size: 9.5px; line-height: 1.65; font-weight: 400; color: var(--ink);
    text-align: justify;
  }
  .intro p + p { margin-top: 10px; }
  .byline {
    position: absolute; left: 72px; top: 600px;
    color: var(--ink);
  }
  .byline .author { font-size: 15px; font-weight: 400; }
  .byline .role { margin-top: 10px; font-size: 10.5px; line-height: 1.6; color: var(--ink-soft); }
  .brand {
    position: absolute; right: 40px; top: 742px;
    display: flex; align-items: center; gap: 8px;
    font-size: 15px; font-weight: 700; color: var(--brand-navy);
    text-transform: uppercase; line-height: 1;
  }
  .brand-dot { width: 28px; height: 28px; border-radius: 50%; background: var(--brand-blue); }
  .contact {
    position: absolute; left: 40px; top: 800px; right: 40px;
    display: flex; gap: 60px;
    font-size: 7.5px; line-height: 1.55; color: var(--ink-soft);
  }
  .contact h4 { font-size: 7.5px; font-weight: 700; color: var(--brand-blue); }
  .footer-band {
    position: absolute; left: 0; bottom: 0; width: 100%; height: 14px;
    background: var(--brand-blue);
  }
</style>
</head>
<body>
  <article class="page">
    <div class="hero-photo" role="img" aria-label="Photo of a doubtful bearded man beside a chalkboard with rows of yellow chalk star ratings and tick boxes"></div>
    <div class="social-tab"></div>
    <div class="running-head">Are you satisfied with your DITA solution?</div>

    <div class="title-disc"></div>
    <h1 class="title">Are you satisfied<br>with your DITA<br>solution?</h1>

    <div class="intro">
      <p>If your answer is “No” then you are not alone according to a 2017 survey of more than 250 technical communication professionals conducted by The Doc Herder. The DITA Satisfaction Survey[1] indicates that 62% of respondents using DITA are—to varying degrees—dissatisfied. As many as 10% of that group were very dissatisfied reporting that their DITA implementation is experiencing ‘big’ challenges. It’s not surprising that there’s significant dissatisfaction amongst those who have adopted DITA. After all, moving to DITA is a seismic shift in technical writing; a big change with many opportunities for things to go wrong.</p>
      <p>The good news is that most DITA users don’t see their problems as insurmountable. Many just need a little help getting to where they’d like to be.</p>
    </div>

    <div class="byline">
      <div class="author">By Dale Morrow</div>
      <div class="role">President of Brightquill Pages<br>Authoring Solutions Inc.</div>
    </div>

    <div class="brand"><span class="brand-dot"></span>Brightquill Pages</div>

    <footer class="contact">
      <div>
        <h4>Head Office</h4>
        410 Lumen Ave, 2nd Floor<br>Brookfield, Ontario<br>K4R 2T9 Canada
      </div>
      <div>
        <h4>Technical Support</h4>
        Call: +1 (555) 014-2290, Press 1#<br>email: help@brightquillpages.com
      </div>
      <div>
        <br>hello@brightquillpages.com<br>www.brightquillpages.com
      </div>
    </footer>
    <div class="footer-band"></div>
  </article>
</body>
</html>
```